Tellmora Corporate Stationery

Look for design of all new corporate stationery for an existing insurance broking business that is going through a redesign and move from older partners to younger family members. New Logo is attached. Company is Brisbane based.
Colours in the Logo is Hex #43bed8 and website features a lot of hex #17b8d8. Website front page "A plan to protect you" - headline. "Professional and Individual advice to protect your greatest assets" - tagline.

Stationery required: Business Cards, Letter head, Thank-you cards, Birthday cards, Presentation folders, With Compliment slips and a powerpoint template. We also would like to send a card to all customers with the something along of the lines of "something new".

Target Market(s)

Customers of Insurance business looking at superannuation, life and income protection insurance, investment advice and wills

Industry/Entity Type

Insurance Broker

Font styles to use
Other font styles liked:
• same as logo

Requirements
Must have
• The above designs for new stationery for the new business including:
• Business Cards, Letter head, Thank-you cards, Birthday cards, Presentation folders, With Compliment slips and a powerpoint template. We also would like to send a card to all customers with the something along of the lines of "something new".
Nice to have
• It is a new look - long time family business being passed to next generation - big focus on advice for YOU, individual advice etc..

```html
<!DOCTYPE html>
<html lang="en">
<head>
<meta charset="utf-8">
<title>Tellmora Financial Group – Letterhead</title>
<link href="https://fonts.googleapis.com/css2?family=Questrial&display=swap" rel="stylesheet">
<style>
  :root {
    --backdrop: #bfe7ea;
    --paper: #ffffff;
    --paper-shade: #f4f8f8;
    --brand-blue: #43bed8;
    --band-blue: #17a9c8;
    --band-grey: #8e8e8e;
    --text-grey: #6d6e70;
    --tint: #e3f2f5;
  }
  * { box-sizing: border-box; margin: 0; padding: 0; }
  html, body { width: 1200px; height: 784px; overflow: hidden; }
  body {
    background: var(--backdrop);
    font-family: "Questrial", sans-serif;
    display: flex; align-items: center; justify-content: center;
  }
  .letterhead {
    position: relative;
    width: 524px; height: 740px;
    background: radial-gradient(ellipse at 55% 50%, var(--paper) 40%, var(--paper-shade) 100%);
    box-shadow: 0 4px 18px rgba(40, 110, 120, .18);
    overflow: hidden;
  }
  .brand {
    position: absolute; top: 34px; left: 36px;
    display: flex; align-items: center; gap: 8px;
  }
  .brand-dot { width: 22px; height: 22px; border-radius: 50%; background: var(--text-grey); }
  .brand-name { color: var(--brand-blue); font-size: 22px; letter-spacing: 1px; line-height: 1; }
  .brand-sub { color: var(--text-grey); font-size: 9px; letter-spacing: 1.6px; margin-top: 3px; }

  .contact-tint { position: absolute; background: var(--tint); opacity: .8; }
  .contact-tint.t1 { top: 28px; right: 18px; width: 60px; height: 44px; }
  .contact-tint.t2 { top: 78px; right: 54px; width: 40px; height: 30px; }
  .contact-tint.t3 { top: 92px; right: 14px; width: 70px; height: 62px; }

  .contact {
    position: absolute; top: 36px; right: 30px;
    font-style: normal;
    font-size: 7px; color: var(--text-grey); line-height: 1.65; text-align: left;
  }
  .contact-title { color: var(--brand-blue); font-size: 8.5px; letter-spacing: .6px; margin-bottom: 2px; }
  .contact-line { display: flex; align-items: center; gap: 4px; white-space: nowrap; }
  .contact-line svg { width: 7px; height: 7px; flex: none; }

  .tagline {
    position: absolute; left: 36px; bottom: 24px;
    color: var(--brand-blue); font-size: 7px; letter-spacing: .7px;
    text-transform: uppercase; white-space: nowrap;
  }
  .footer-band { position: absolute; left: 0; bottom: 0; height: 9px; }
  .footer-band.blue { width: 84%; background: var(--band-blue); }
  .footer-band.grey { left: 85.5%; right: 0; background: linear-gradient(90deg, #b5b5b5, var(--band-grey)); }
</style>
</head>
<body>
  <main class="letterhead">
    <header class="brand">
      <span class="brand-dot"></span>
      <div>
        <div class="brand-name">TELLMORA</div>
        <div class="brand-sub">FINANCIAL GROUP</div>
      </div>
    </header>

    <div class="contact-tint t1"></div>
    <div class="contact-tint t2"></div>
    <div class="contact-tint t3"></div>

    <address class="contact">
      <div class="contact-title">TELLMORA FINANCIAL GROUP</div>
      <div class="contact-line">
        <svg viewBox="0 0 10 10"><path d="M5 0a3.5 3.5 0 0 0-3.5 3.5C1.5 6 5 10 5 10s3.5-4 3.5-6.5A3.5 3.5 0 0 0 5 0zm0 5a1.5 1.5 0 1 1 0-3 1.5 1.5 0 0 1 0 3z" fill="#43bed8"/></svg>
        Harbour Lane, Suite 240 Brisbane, QLD 4000
      </div>
      <div class="contact-line">
        <svg viewBox="0 0 10 10"><circle cx="5" cy="5" r="5" fill="#43bed8"/><path d="M3.3 2.5l1 1-.5.7c.4.8 1 1.4 1.8 1.8l.7-.5 1 1-.7.9C4.8 7.2 2.8 5.2 2.5 3.2z" fill="#fff"/></svg>
        (07) 3000 4162
      </div>
      <div class="contact-line">
        <svg viewBox="0 0 10 10"><circle cx="5" cy="5" r="5" fill="#43bed8"/><rect x="2.7" y="3.2" width="4.6" height="3.6" fill="#fff"/></svg>
        (07) 3000 5398
      </div>
      <div class="contact-line">
        <svg viewBox="0 0 10 10"><circle cx="5" cy="5" r="5" fill="#43bed8"/><circle cx="5" cy="5" r="2.6" fill="none" stroke="#fff" stroke-width=".8"/></svg>
        www.tellmorafinancialgroup.com
      </div>
    </address>

    <p class="tagline">A plan built around you &nbsp;-&nbsp; Personal and tailored guidance to secure what matters most</p>
    <div class="footer-band blue"></div>
    <div class="footer-band grey"></div>
  </main>
</body>
</html>
```